Website for a service provided by a Canadian Immigration Company

Design and Code a website for a Canadian immigration company which provides service to clients all across the world. the website should be very Canadian centric and have 4-5 pages. Basic, classy modern. I have the logo s already designed. Please contact me and I can send you some more details. It's basically a service which is provided to clients who are below 17 and need a guardian in canada to sign their documents that they will be looked after them. It's called custodianship. You can google the term and you will understand what it means
Updates

didn't realize it was just a day

Target Market(s)

17-55

Industry/Entity Type

Immigration

Coding

Coded - Design and coding required

Number of Pages Required

5+ page

Font styles to use
Sans Serif

Colors
EE7325
F08F49
F5BC92
FAE3D3
FDF4ED
EB3D1F
EC4F4E
F09395
F8D3D4
FCEDEE

Requirements
Must have
• Pages with some graphics, some small animations like clients served, projects completed

```html
<!DOCTYPE html>
<html lang="en">
<head>
<meta charset="utf-8">
<title>Wardhaven – Custodianship for Minor Students in Canada</title>
<link href="https://fonts.googleapis.com/css2?family=Montserrat:wght@300;400;500&family=Ubuntu:wght@500;700&display=swap" rel="stylesheet">
<style>
:root{
  --red:#eb3d1f;
  --red-soft:#ec4f4e;
  --orange:#ee7325;
  --pink:#f8d3d4;
  --pink-light:#fcedee;
  --peach:#fae3d3;
  --ink:#1b1b1b;
  --text:#3c3c3c;
  --grey-bg:#f3f3f3;
  --dark:#1e1e1e;
  --white:#fff;
}
*{box-sizing:border-box;margin:0;padding:0}
html,body{width:1200px;height:4155px;overflow:hidden}
body{position:relative;font-family:"Montserrat",sans-serif;font-weight:300;color:var(--text);background:#f7f7f7}
.abs{position:absolute}
h1,h2,h3{font-family:"Ubuntu",sans-serif;font-weight:500;color:var(--ink)}
.btn{position:absolute;display:flex;align-items:center;justify-content:center;background:var(--red);color:var(--white);font-family:"Montserrat",sans-serif;font-weight:400;font-size:17px;border-radius:5px}
p{font-size:17px;line-height:29px}

.topbar{left:0;top:0;width:1200px;height:48px;background:var(--dark);color:#eee;font-weight:400;font-size:16px}
.topbar .mail{left:113px;top:13px;display:flex;align-items:center;gap:10px}
.topbar .social{right:110px;top:17px;display:flex;gap:14px}
.dot{width:14px;height:14px;border-radius:50%;background:#eee}

.header{left:0;top:48px;width:1200px;height:105px;background:var(--white)}
.brand{display:flex;align-items:center;gap:10px;font-family:"Montserrat",sans-serif;font-weight:500;font-size:24px;color:var(--ink)}
.brand .mark{width:30px;height:30px;border-radius:50%;background:var(--red)}
.header .brand{position:absolute;left:113px;top:36px}
.nav{left:492px;top:42px;display:flex;gap:48px;font-size:17px;font-weight:400;color:var(--ink)}
.nav .active{color:var(--red)}

.hero{left:0;top:153px;width:1200px;height:466px;background:linear-gradient(100deg,#e7a9a6 0%,#f1d7d6 22%,#e8e4e2 45%,#b9a9a4 62%,#d88d8a 75%,#c9c4c2 88%,#a7a19f 100%)}
.hero .welcome{left:111px;top:103px;font-family:"Ubuntu",sans-serif;font-size:30px;font-weight:500;line-height:36px;color:var(--ink)}
.hero .name{left:109px;top:136px;font-family:"Ubuntu",sans-serif;font-size:52px;font-weight:700;line-height:60px;color:var(--ink)}
.hero .tagline{left:111px;top:210px;width:440px;color:#2a2a2a;font-weight:400;font-size:16.5px;line-height:29px}

.about{left:0;top:619px;width:1200px;height:631px;background:var(--grey-bg)}
.circle{position:absolute;border-radius:50%}
.photo-about{left:13px;top:123px;width:447px;height:436px;background:linear-gradient(135deg,#e7e2d9,#c9b9a4 50%,#8aa0b4);border-right:8px solid var(--orange);border-bottom-left-radius:420px}
.about h2{position:absolute;left:521px;top:150px;font-size:36px}
.about p{position:absolute;left:521px;top:222px;width:568px;text-align:justify}

.whatwedo{left:0;top:1250px;width:1200px;height:800px}
.title-center{position:absolute;width:1200px;text-align:center;font-size:36px}
.title-center span{border-bottom:3px solid var(--red);padding-bottom:2px}
.whatwedo .lead{left:110px;top:172px;width:980px;text-align:center;font-size:16.5px}
.service{position:absolute;top:460px;width:280px}
.service svg{display:block}
.service h3{font-size:23px;margin-top:14px}
.service p{margin-top:12px;font-size:16.5px}

.minor h2{position:absolute;left:116px;top:2130px;font-size:36px}
.minor p.body{position:absolute;left:116px;top:2202px;width:560px;text-align:justify}
.photo-minor{left:724px;top:2089px;width:463px;height:435px;background:linear-gradient(135deg,#a7a197,#7f8a93 45%,#c2b49a);border-left:8px solid var(--orange);border-bottom-right-radius:420px}

.faq-bg{left:0;top:2637px;width:1200px;height:710px;background:#f1f1f1}
.faq{left:115px;top:2786px;width:977px;height:427px;border-left:5px solid var(--red);background:linear-gradient(90deg,#f7dcd4,#f6e3de 60%,#f3e6e3)}
.faq .row{position:absolute;left:0;width:972px;display:flex;align-items:center}
.faq .letter{position:absolute;left:17px;font-family:"Ubuntu",sans-serif;font-weight:500;font-size:34px;color:var(--ink)}
.faq .q{font-size:22px;font-weight:400;color:var(--ink);margin-left:86px}
.faq .a{font-size:16.5px;line-height:29px;margin-left:86px;width:820px;color:var(--ink)}
.faq .qrow{background:rgba(241,194,178,.45)}

.contact h2{position:absolute;left:103px;top:3465px;font-size:40px}
.contact h2 span{border-bottom:2px solid var(--red)}
.contact .social{left:103px;top:3572px;display:flex;gap:22px}
.contact .social .dot{width:28px;height:28px;background:var(--red)}

.footer{left:0;top:3683px;width:1200px;height:337px;background:linear-gradient(110deg,#eb3d1f,#ec4f4e 55%,#eb3d1f)}
.footer .brand{position:absolute;left:106px;top:73px;color:var(--white);font-size:31px;font-weight:400}
.footer .brand .mark{background:var(--white);width:38px;height:38px}
.footer p{position:absolute;left:113px;top:163px;width:330px;color:var(--white);font-weight:400}
.footnav{left:0;top:4020px;width:1200px;height:61px;background:#ef6b5e;display:flex;justify-content:center;align-items:center;gap:54px;color:var(--white);font-size:15px;font-weight:400}
.copy{left:0;top:4081px;width:1200px;height:74px;background:var(--red);color:var(--white);font-size:12.5px;font-weight:400}
.copy span{position:absolute;left:111px;top:26px}

.form-card{left:506px;top:3420px;width:601px;height:567px;background:var(--white);border-radius:24px;box-shadow:0 4px 30px rgba(0,0,0,.12)}
.field{position:absolute;left:46px;width:509px;height:42px;border:2px solid #cfcfcf;border-radius:21px;font-size:14px;color:#999;padding:10px 22px;font-weight:400}
.field.msg{height:130px;border-radius:22px}
</style>
</head>
<body>

<div class="abs topbar">
  <div class="abs mail">
    <svg width="18" height="14" viewBox="0 0 18 14"><rect x="0.5" y="0.5" width="17" height="13" rx="1.5" fill="#eee"/><path d="M1 1.5 9 8l8-6.5" stroke="#1e1e1e" stroke-width="1.5" fill="none"/></svg>
    info@wardhaven.com
  </div>
  <div class="abs social"><span class="dot"></span><span class="dot"></span><span class="dot"></span></div>
</div>

<header class="abs header">
  <div class="brand"><span class="mark"></span>wardhaven.ca</div>
  <nav class="abs nav"><span class="active">Home</span><span>Services</span><span>Contact Us</span></nav>
  <span class="btn" style="left:932px;top:34px;width:157px;height:49px">Book Online</span>
</header>

<section class="abs hero" role="img" aria-label="Smiling student holding notebooks in front of a Canadian city skyline with a maple leaf flag">
  <div class="abs welcome">Welcome to</div>
  <div class="abs name">Wardhaven</div>
  <p class="abs tagline">Lorem ipsum dolor sit amet, consectetur adipiscing<br>elit, sed do eiusmod tempor incididunt.</p>
  <span class="btn" style="left:111px;top:284px;width:157px;height:48px">Get Started</span>
</section>

<section class="abs about">
  <div class="circle" style="left:-90px;top:520px;width:250px;height:250px;background:rgba(240,147,149,.35)"></div>
  <div class="abs photo-about" role="img" aria-label="Three school children carrying folders in a school hallway"></div>
  <h2>About Us</h2>
  <p>Lorem ipsum dolor sit amet, consectetur adipiscing elit, sed do eiusmod tempor incididunt ut labore et dolore magna aliqua. Quis ipsum suspendisse ultrices gravida. Risus commodo viverra maecenas accumsan lacus vel facilisis. Lorem ipsum dolor sit amet, consectetur adipiscing elit, sed do eiusmod tempor incididunt ut labore et dolore magna aliqua. Quis ipsum suspendisse ultrices gravida. Risus commodo viverra maecenas accumsan lacus vel facilisis.</p>
  <span class="btn" style="left:519px;top:463px;width:155px;height:49px">Read More</span>
</section>

<section class="abs whatwedo">
  <div class="circle" style="left:1120px;top:240px;width:260px;height:330px;background:rgba(240,147,149,.25)"></div>
  <h2 class="title-center" style="top:86px">What <span>We Do</span></h2>
  <p class="abs lead">We provide the required signed and notarized custodian declaration along with formal supervision service upon the student's arrival in Canada. According to Citizenship and Immigration Canada (IRCC), minor students can be accepted at a university or college, but they cannot obtain a study permit without the required signed and notarized custodianship form.<br>We provide support for minor international students in Canada and peace of mind for their parents. Our warm and kindhearted Legal Custodian will guide international students through their first challenging months in a new environment. We communicate with parents to discuss their children's emotional and academic needs to ensure they achieve success, academically and personally in Canada.</p>

  <div class="service" style="left:134px">
    <svg width="72" height="72" viewBox="0 0 72 72" fill="none" stroke="#eb3d1f" stroke-width="2.5"><rect x="4" y="12" width="36" height="54" rx="3"/><circle cx="22" cy="36" r="10"/><path d="M12 36h20M22 26c-5 6-5 14 0 20M22 26c5 6 5 14 0 20"/><rect x="38" y="4" width="24" height="40" rx="3" transform="rotate(15 50 24)"/></svg>
    <h3>Visa</h3>
    <p>Lorem ipsum dolor sit amet, adipiscing elit, sed do eiusmod tempor incididunt ut labore et.</p>
  </div>
  <div class="service" style="left:484px">
    <svg width="72" height="72" viewBox="0 0 72 72" fill="none" stroke="#eb3d1f" stroke-width="2.5"><rect x="6" y="6" width="56" height="60" rx="4"/><path d="M6 22h56"/><circle cx="24" cy="44" r="8"/><path d="M38 38h16M38 46h16M38 54h10"/></svg>
    <h3>Passport</h3>
    <p>Lorem ipsum dolor sit amet, adipiscing elit, sed do eiusmod tempor incididunt ut labore et.</p>
  </div>
  <div class="service" style="left:834px">
    <svg width="72" height="72" viewBox="0 0 72 72" fill="none" stroke="#eb3d1f" stroke-width="2.5"><rect x="26" y="8" width="40" height="56" rx="3"/><circle cx="48" cy="24" r="8"/><path d="M44 24l3 3 5-6M34 42h24M34 50h24"/><circle cx="16" cy="34" r="9"/><path d="M4 64c0-12 6-18 12-18s12 6 12 18"/></svg>
    <h3>Visa</h3>
    <p>Lorem ipsum dolor sit amet, adipiscing elit, sed do eiusmod tempor incididunt ut labore et.</p>
  </div>
</section>

<section class="minor">
  <h2>Studying in Canada as a <span style="border-bottom:3px solid var(--red)">Minor</span></h2>
  <p class="body">It's basically a service which is provided to clients who are below 17 and need a guardian in Canada to sign their documents so that they will be looked after them. It's called custodianship. You can google the term and you will understand what it means.<br>It's basically a service which is provided to clients who are below 17 and need a guardian in Canada to sign their documents so that they will be looked after them. It's called custodianship. You can google the term and you will understand what it means.</p>
  <span class="btn" style="left:118px;top:2463px;width:156px;height:48px">Learn More</span>
  <div class="abs photo-minor" role="img" aria-label="A young woman and a boy sitting on a sofa reviewing papers with an advisor"></div>
</section>

<div class="abs faq-bg"></div>
<div class="circle" style="left:-60px;top:2580px;width:180px;height:180px;background:rgba(240,147,149,.35)"></div>
<h2 class="title-center" style="top:2680px">FAQ<span>s</span></h2>
<div class="abs faq">
  <div class="row qrow" style="top:0;height:85px"><span class="letter">Q.</span><span class="q">Below 17 Years and is it need a guardian to study in Canada?</span></div>
  <div class="row" style="top:85px;height:126px"><span class="letter">A.</span><span class="a">Lorem ipsum dolor sit amet, consectetur adipiscing elit, sed do eiusmod tempor incididunt ut labore et dolore magna aliqua. Quis ipsum suspendisse ultrices gravida. Risus commodo viverra maecenas accumsan lacus vel facilisis.</span></div>
  <div class="row qrow" style="top:211px;height:89px"><span class="letter">Q.</span><span class="q">Below 17 Years and is it need a guardian to study in Canada?</span></div>
  <div class="row" style="top:300px;height:127px"><span class="letter">A.</span><span class="a">Lorem ipsum dolor sit amet, consectetur adipiscing elit, sed do eiusmod tempor incididunt ut labore et dolore magna aliqua. Quis ipsum suspendisse ultrices gravida. Risus commodo viverra maecenas accumsan lacus vel facilisis.</span></div>
</div>
<span class="btn" style="left:529px;top:3253px;width:140px;height:47px">View More</span>

<section class="contact">
  <h2>Contact <span>Us</span></h2>
  <div class="abs social"><span class="dot"></span><span class="dot"></span><span class="dot"></span></div>
</section>

<footer class="abs footer">
  <div class="brand"><span class="mark"></span>wardhaven.ca</div>
  <p>Lorem ipsum dolor sit amet, consectetur adipiscing elit, sed do eiusmod tempor ut let dolore magna aliqua.</p>
</footer>
<div class="abs footnav"><span>HOME</span><span>SERVICES</span><span>CONTACT US</span></div>
<div class="abs copy"><span>© copyrights 2023 wardhaven.ca | All Rights Reserved</span></div>

<form class="abs form-card">
  <div class="field" style="top:45px">First Name</div>
  <div class="field" style="top:114px">Last Name</div>
  <div class="field" style="top:183px">Phone Number</div>
  <div class="field" style="top:251px">Email</div>
  <div class="field msg" style="top:322px">Message</div>
  <span class="btn" style="left:47px;top:479px;width:141px;height:46px">Submit</span>
</form>

</body>
</html>
```